Corvane Business Cards

Front of business card will have logo, name, address, & telephone number. Back of card will have a list of services provided - Roads, Substation Pads, Temporary Pads, Site Pads, Land Leveling, Powerline Row Cleaning, Land Clearing, Gates, Fencing, Construction Entrances, Excavation, Trenching, Underground Utilities, Directional Boring, Pile Driving. We are a construction company that uses heavy equipment like bulldozers, motor graders/blades, dump trucks, backhoes, hydro axes, & skid loaders. We build roads, pads, & install electric utility lines & waterlines underground. This logo is new. The word "Construction" can be smaller as uploaded 2 example edited logos. We will be using this card design for many employees.
Target Market(s)
Industrial Electric Powerline, Wind Turbine, Solar Panel, & Water Utility companies.
Contact Information for Business Card
Name/Position - Dwayne Halster - Owner
Address: 4875 Route 309
Calder Springs, OK 73510
Phone number - (555) 482-5096

```html
<!DOCTYPE html>
<html lang="en">
<head>
<meta charset="utf-8">
<title>Corvane Construction Business Cards</title>
<link href="https://fonts.googleapis.com/css2?family=Montserrat:wght@400;500;600;700&display=swap" rel="stylesheet">
<style>
  :root {
    --maroon: #3f0f19;
    --maroon-text: #4a1520;
    --white: #ffffff;
    --stage: #1e1e1f;
    --ink-soft: #5a3a40;
  }
  * { margin: 0; padding: 0; box-sizing: border-box; }
  html, body { width: 1200px; height: 852px; overflow: hidden; }
  body {
    background: var(--stage);
    font-family: "Montserrat", Arial, sans-serif;
    position: relative;
  }
  .card {
    position: absolute;
    width: 600px;
    height: 343px;
    border-radius: 22px;
    overflow: hidden;
  }
  .card-services {
    left: 80px; top: 90px;
    background: var(--maroon);
    color: var(--white);
  }
  .card-contact {
    left: 520px; top: 420px;
    background: var(--white);
    color: var(--maroon-text);
    box-shadow: 0 10px 30px rgba(0,0,0,0.5);
  }

  /* services side */
  .brand-mark {
    position: absolute;
    left: 0; right: 0; top: 34px;
    text-align: center;
    font-weight: 700;
    color: var(--white);
  }
  .brand-mark .brand-name {
    display: block;
    font-size: 44px;
    letter-spacing: 6px;
    line-height: 1;
  }
  .brand-mark .brand-sub {
    display: block;
    margin-top: 10px;
    font-size: 36px;
    letter-spacing: 3px;
    line-height: 1;
  }
  .services {
    position: absolute;
    left: 34px; right: 20px; top: 168px;
    display: flex;
    gap: 20px;
    font-size: 15px;
    line-height: 1.45;
  }
  .services-heading { font-weight: 600; font-size: 15px; }
  .service-list { list-style: none; }
  .service-list li { position: relative; padding-left: 16px; white-space: nowrap; }
  .service-list li::before {
    content: "";
    position: absolute; left: 0; top: 8px;
    width: 6px; height: 6px; border-radius: 50%;
    background: var(--white);
  }
  .col-first .service-list { padding-left: 10px; }

  /* contact side */
  .contact-brand {
    position: absolute;
    left: 40px; top: 138px;
    width: 250px;
    text-align: center;
    font-weight: 700;
    color: var(--maroon);
  }
  .contact-brand .brand-name { display: block; font-size: 40px; letter-spacing: 4px; line-height: 1; }
  .contact-brand .brand-sub { display: block; font-size: 17px; letter-spacing: 3px; margin-top: 8px; }
  .divider {
    position: absolute;
    left: 318px; top: 96px;
    width: 2px; height: 150px;
    background: var(--maroon);
  }
  .contact-details {
    position: absolute;
    left: 346px; top: 104px;
    right: 16px;
  }
  .person-name { font-size: 20px; font-weight: 600; letter-spacing: 1px; }
  .person-role { font-size: 14px; color: var(--ink-soft); margin-bottom: 10px; }
  .contact-line {
    display: flex; align-items: flex-start; gap: 8px;
    font-size: 16px; line-height: 1.35;
    white-space: nowrap;
  }
  .contact-line svg { flex: none; margin-top: 3px; }
</style>
</head>
<body>

<section class="card card-services" aria-label="Business card, services side">
  <div class="brand-mark">
    <span class="brand-name">CORVANE</span>
    <span class="brand-sub">CONSTRUCTION</span>
  </div>
  <div class="services">
    <div class="col-first">
      <div class="services-heading">Services:</div>
      <ul class="service-list">
        <li>Roads</li>
        <li>Site Pads</li>
        <li>Gates</li>
        <li>Fencing</li>
      </ul>
    </div>
    <div class="col-second">
      <ul class="service-list">
        <li>Trenching</li>
        <li>Temporary Pads</li>
        <li>Land Leveling</li>
        <li>Land Clearing</li>
        <li>Substation Pads</li>
      </ul>
    </div>
    <div class="col-third">
      <ul class="service-list">
        <li>Powerline Row Cleaning</li>
        <li>Construction Entrances</li>
        <li>Excavation</li>
        <li>Underground Utilities</li>
        <li>Directional Boring, Pile Driving</li>
      </ul>
    </div>
  </div>
</section>

<section class="card card-contact" aria-label="Business card, contact side">
  <div class="contact-brand">
    <span class="brand-name">CORVANE</span>
    <span class="brand-sub">CONSTRUCTION</span>
  </div>
  <div class="divider"></div>
  <div class="contact-details">
    <div class="person-name">DWAYNE HALSTER</div>
    <div class="person-role">owner</div>
    <div class="contact-line">
      <svg width="14" height="14" viewBox="0 0 24 24" aria-hidden="true">
        <path fill="#3f0f19" d="M6.6 10.8a15.1 15.1 0 0 0 6.6 6.6l2.2-2.2c.3-.3.7-.4 1-.2 1.1.4 2.3.6 3.6.6.6 0 1 .4 1 1V20c0 .6-.4 1-1 1C10.6 21 3 13.4 3 4c0-.6.4-1 1-1h3.5c.6 0 1 .4 1 1 0 1.3.2 2.5.6 3.6.1.3 0 .7-.2 1z"/>
      </svg>
      <span>(555) 482-5096</span>
    </div>
    <div class="contact-line">
      <svg width="14" height="16" viewBox="0 0 24 28" aria-hidden="true">
        <path fill="#3f0f19" d="M12 0C6.5 0 2 4.4 2 9.9 2 17.3 12 28 12 28s10-10.7 10-18.1C22 4.4 17.5 0 12 0zm0 13.5a3.6 3.6 0 1 1 0-7.2 3.6 3.6 0 0 1 0 7.2z"/>
      </svg>
      <span>4875 Route 309<br>Calder Springs, OK 73510</span>
    </div>
  </div>
</section>

</body>
</html>
```